Boutique custom software development company needs new business card

Our nearly 20 year old custom software development company would like to better include the fact that we are now providing Bitcoin services. These new services are B2B include education (how to acquire and securely hold Bitcoin) and integrating Bitcoin payments into existing ecommerce sites or other existing systems. Please keep the card clean and simple. Attached is our current design and some other files. vextorial.com

Target Market(s)

businesses owners interested in long term relationship

Industry/Entity Type

Custom software development and Bitcoin

Contact Information for Business Card

Dale Parker, dale@vextorial.com, vextorial.com, (888) 555-VXTRL

Font styles to use
Other font styles liked:
• monospace

Requirements
Must have
• double-sided
Nice to have
• clean and simple
Should not have
• physical address

```html
<!DOCTYPE html>
<html lang="en">
<head>
<meta charset="utf-8">
<title>Vextorial Business Card</title>
<link href="https://fonts.googleapis.com/css2?family=Montserrat:wght@400;700;800&family=Lato:wght@400&display=swap" rel="stylesheet">
<style>
  :root {
    --backdrop: #e8e3da;
    --card-white: #ffffff;
    --brand-blue: #3d72bb;
    --brand-blue-dark: #2d5c9c;
    --brand-blue-light: #b9cdea;
    --text-gray: #555a60;
    --text-dark: #222428;
  }
  * { margin: 0; padding: 0; box-sizing: border-box; }
  html, body {
    width: 900px; height: 1200px; overflow: hidden;
    background: var(--backdrop);
  }
  .canvas { position: relative; width: 900px; height: 1200px; }

  .card {
    position: absolute; left: 80px; width: 742px; height: 440px;
    border-radius: 30px; overflow: hidden;
    box-shadow: 0 6px 14px rgba(0,0,0,0.25);
  }
  .card-front { top: 132px; background: var(--card-white); }
  .card-back { top: 640px; background: var(--brand-blue); }

  .front-band {
    position: absolute; left: 0; right: 0; bottom: 0; height: 14px;
    background: var(--brand-blue);
  }

  .brand-square {
    position: absolute; left: 104px; top: 109px; width: 124px; height: 122px;
    background: var(--brand-blue);
  }
  .brand-name {
    position: absolute; left: 262px; top: 118px;
    font-family: "Montserrat", sans-serif; font-weight: 800;
    font-size: 64px; letter-spacing: 1px; line-height: 1;
    color: var(--brand-blue); text-transform: uppercase;
  }
  .brand-tagline {
    position: absolute; left: 275px; top: 196px;
    font-family: "Lato", sans-serif; font-size: 21px;
    color: var(--brand-blue); white-space: nowrap;
  }

  .person {
    position: absolute; right: 414px; top: 302px; text-align: right;
    font-family: "Montserrat", sans-serif;
  }
  .person-name { font-size: 26px; font-weight: 700; color: var(--brand-blue); line-height: 1.15; }
  .person-role { font-size: 16px; color: var(--text-gray); margin-top: 2px; }

  .divider {
    position: absolute; left: 362px; top: 298px; width: 2px; height: 58px;
    background: var(--brand-blue);
  }

  .contact-list {
    position: absolute; left: 390px; top: 294px; list-style: none;
    font-family: "Montserrat", sans-serif; font-size: 16px; color: var(--text-dark);
  }
  .contact-list li { display: flex; align-items: center; height: 22px; }
  .contact-list svg { width: 12px; height: 12px; margin-right: 13px; fill: var(--brand-blue); }

  .back-name {
    position: absolute; left: 0; right: 0; top: 128px; text-align: center;
    font-family: "Montserrat", sans-serif; font-weight: 800;
    font-size: 100px; letter-spacing: 2px; line-height: 1;
    color: var(--brand-blue-dark); text-transform: uppercase;
  }
  .back-tagline {
    position: absolute; left: 0; right: 0; top: 258px; text-align: center;
    font-family: "Lato", sans-serif; font-size: 35px;
    color: var(--brand-blue-light);
  }
</style>
</head>
<body>
<main class="canvas">
  <section class="card card-front">
    <div class="brand-square"></div>
    <div class="brand-name">Vextorial</div>
    <div class="brand-tagline">developer of custom applications</div>

    <div class="person">
      <div class="person-name">Dale Parker</div>
      <div class="person-role">Owner</div>
    </div>
    <div class="divider"></div>
    <ul class="contact-list">
      <li>
        <svg viewBox="0 0 12 12" aria-hidden="true"><path d="M1 4c0-1.5 2-2.5 5-2.5S11 2.5 11 4v1H8.5V3.8h-5V5H1z"/><rect x="2.5" y="6" width="7" height="5" rx="1"/></svg>
        (888) 555-VXTRL
      </li>
      <li>
        <svg viewBox="0 0 12 12" aria-hidden="true"><path d="M0 2h12v1L6 7 0 3z"/><path d="M0 4.2l6 4 6-4V10H0z"/></svg>
        dale@vextorial.com
      </li>
      <li>
        <svg viewBox="0 0 12 12" aria-hidden="true"><circle cx="6" cy="6" r="5.5"/><path d="M4 3h3l1 2-2 1-1 3-1-3-1-1z" fill="#fff"/></svg>
        www.vextorial.com
      </li>
    </ul>
    <div class="front-band"></div>
  </section>

  <section class="card card-back">
    <div class="back-name">Vextorial</div>
    <div class="back-tagline">developer of custom applications</div>
  </section>
</main>
</body>
</html>
```